Website Homepage Design

Tarvento Care Partners Inc. is a Canadian financial services company that specialize in the delivery and administration of alternative health benefit solutions. Tarvento is seeking to adjust their brand and develop a new website.

We like the design and layout of the website below but are not looking for an exact replica (be creative):

http://www.quellaroforum.example/

We want the colour scheme to be clean white and "fresh green", possibly with orange accents (links).

This posting is only for a website homepage design (no coding), but anyone who includes a new logo, in addition to the design, will get priority.

Best of luck,

Orrin
Updates

Project is guaranteed.

Please let me know if you are currently working on a design.

Thank you,

Orrin

*Update:

Two example websites with good colour scheme/design:

- http://blimeden.example/
- http://www.faltrukidscove.example.au/

I have attached a wireframe and colour scheme to the project brief. The main colour should be the green one. Other colours can be used for highlights and accents, etc.

Target Market(s)

Business owners age 50+

Industry/Entity Type

Financial

Requirements
Must have
• - Clear and simple design
- Area for video (similar to http://www.quellaroforum.example)
Should not have
• - Lots of pictures

```html
<!DOCTYPE html>
<html lang="en">
<head>
<meta charset="utf-8">
<title>Tarvento – Home</title>
<link rel="stylesheet" href="https://fonts.googleapis.com/css2?family=Nunito:wght@400;800;900&family=Arimo:wght@400;700&display=swap">
<style>
  :root {
    --green: #8fbc1a;
    --green-dark: #6e9c10;
    --green-light: #a9cc2a;
    --leaf: #5aa520;
    --page: #efefef;
    --header: #ececec;
    --ink: #333333;
    --white: #ffffff;
    --orange: #ff7a10;
    --orange-light: #ff9a2a;
    --blue: #2f8fc6;
    --blue-light: #3ea7da;
    --video: #0b0f14;
  }
  * { margin: 0; padding: 0; box-sizing: border-box; }
  html, body { width: 1200px; height: 1050px; overflow: hidden; }
  body {
    position: relative;
    background: var(--page);
    font-family: "Arimo", Arial, sans-serif;
    color: var(--ink);
  }
  .site-header {
    position: absolute; left: 0; top: 0; width: 1200px; height: 127px;
    background: radial-gradient(ellipse 260px 180px at 380px 40px, #ffffff 0%, rgba(255,255,255,0) 100%), var(--header);
  }
  .brand {
    position: absolute; left: 143px; top: 48px;
    display: flex; align-items: center; gap: 8px;
    font-family: "Nunito", sans-serif; font-weight: 800; font-size: 38px;
    color: var(--leaf); letter-spacing: -0.5px;
  }
  .brand-dot { width: 12px; height: 12px; border-radius: 50%; background: var(--orange); }
  .follow {
    position: absolute; left: 862px; top: 47px; width: 208px; height: 38px;
    border-radius: 8px; background: #dedede; border: 1px solid #f6f6f6;
    box-shadow: inset 0 1px 2px rgba(0,0,0,.08);
    display: flex; align-items: center; padding-left: 16px; gap: 8px;
    font-size: 11px; color: #333;
  }
  .follow-label { margin-right: 6px; }
  .social { width: 22px; height: 22px; border-radius: 3px; }
  .social.s1 { background: #3b5da0; }
  .social.s2 { background: #47b7de; }
  .social.s3 { background: #c9262b; }
  .social.s4 { background: #f48a1c; }
  .main-nav {
    position: absolute; left: 0; top: 127px; width: 1200px; height: 38px;
    background: linear-gradient(#9ec62a, #86b412);
    border-bottom: 1px solid #6e9c10;
  }
  .main-nav a {
    position: absolute; top: 11px;
    color: var(--white); text-decoration: none; font-size: 14px;
    text-shadow: 0 1px 1px rgba(0,0,0,.3); white-space: nowrap;
  }
  .video-frame {
    position: absolute; left: 110px; top: 186px; width: 960px; height: 463px;
    background: var(--white); box-shadow: 0 0 4px rgba(0,0,0,.25);
  }
  .video-stage {
    position: absolute; left: 10px; top: 10px; width: 940px; height: 443px;
    background: radial-gradient(ellipse 600px 300px at 700px 200px, #13243a 0%, var(--video) 70%);
    overflow: hidden;
  }
  .buffer {
    position: absolute; left: 437px; top: 171px; width: 67px; height: 67px;
    border-radius: 50%; background: var(--white);
    display: flex; flex-direction: column; align-items: center; justify-content: center;
    font-size: 20px; color: #444;
  }
  .buffer small { font-size: 7px; letter-spacing: 1px; margin-top: 2px; }
  .play {
    position: absolute; left: 438px; top: 369px; width: 65px; height: 41px;
    border-radius: 20px; background: linear-gradient(#ffffff, #d8d8d8);
  }
  .play svg { position: absolute; left: 24px; top: 11px; }
  .cta {
    position: absolute; top: 669px; width: 311px; height: 110px;
    padding: 5px; text-decoration: none;
  }
  .cta-inner {
    height: 100%; border: 1px solid rgba(255,255,255,.35);
    display: flex; flex-direction: column; align-items: center; justify-content: center;
    text-align: center; white-space: nowrap;
    font-family: "Nunito", sans-serif; color: var(--white);
    text-shadow: 0 1px 2px rgba(0,0,0,.25);
    padding-top: 2px;
  }
  .cta-top { font-size: 25px; font-weight: 400; line-height: 30px; }
  .cta-bottom { font-size: 27px; font-weight: 900; line-height: 32px; letter-spacing: -0.2px; }
  .cta.products { left: 110px; background: linear-gradient(#ff6a0a, var(--orange-light)); }
  .cta.tour { left: 435px; background: linear-gradient(#86b412, #a3cc22); }
  .cta.start { left: 759px; background: linear-gradient(#2a83bd, var(--blue-light)); }
  .site-footer {
    position: absolute; left: 0; top: 830px; width: 1200px; height: 220px;
    background: linear-gradient(#93c020, var(--green-light));
  }
  .footer-col { position: absolute; top: 16px; }
  .footer-col h4 { font-size: 12px; font-weight: 700; color: var(--white); margin-bottom: 9px; }
  .footer-col a {
    display: block; font-size: 12px; color: #f5fae6; text-decoration: none;
    line-height: 22px; text-shadow: 0 1px 1px rgba(0,0,0,.15);
  }
  .footer-col.about h4 { margin-bottom: 5px; }
  .footer-col.about a { padding-left: 3px; }
  .footer-brand {
    position: absolute; left: 952px; top: 118px;
    font-family: "Nunito", sans-serif; font-weight: 800; font-size: 25px; color: var(--white);
  }
  .legal {
    position: absolute; right: 143px; top: 161px; text-align: right;
    font-size: 11px; color: var(--white); line-height: 23px;
  }
  .legal a { color: var(--white); text-decoration: none; }
</style>
</head>
<body>
<header class="site-header">
  <div class="brand"><span>Tarvento</span><span class="brand-dot"></span></div>
  <div class="follow">
    <span class="follow-label">Follow Us</span>
    <span class="social s1"></span><span class="social s2"></span><span class="social s3"></span><span class="social s4"></span>
  </div>
</header>
<nav class="main-nav">
  <a href="#" style="left:129px">Home</a>
  <a href="#" style="left:225px">Products</a>
  <a href="#" style="left:341px">Education</a>
  <a href="#" style="left:462px">Clients</a>
  <a href="#" style="left:565px">Company</a>
  <a href="#" style="left:684px">Contact Us</a>
</nav>
<section class="video-frame">
  <div class="video-stage" role="img" aria-label="Introductory video, dark abstract background with light streaks">
    <div class="buffer">0%<small>BUFFERING</small></div>
    <div class="play"><svg width="18" height="20" viewBox="0 0 18 20"><path d="M0 0 L18 10 L0 20 Z" fill="#444"/></svg></div>
  </div>
</section>
<a class="cta products" href="#"><div class="cta-inner"><span class="cta-top">VIEW OUR</span><span class="cta-bottom">PRODUCTS &amp; PRICING</span></div></a>
<a class="cta tour" href="#"><div class="cta-inner"><span class="cta-top">TAKE A</span><span class="cta-bottom">QUICK TOUR
  <svg width="22" height="22" viewBox="0 0 22 22" style="vertical-align:-2px"><circle cx="11" cy="11" r="11" fill="#fff"/><path d="M8 6 L16 11 L8 16 Z" fill="#94c01c"/></svg></span></div></a>
<a class="cta start" href="#"><div class="cta-inner"><span class="cta-top">GET STARTED</span><span class="cta-bottom">READ, DEMO, TALK</span></div></a>
<footer class="site-footer">
  <div class="footer-col about" style="left:109px"><h4>WHO WE ARE</h4><a href="#">About Us</a><a href="#">Meet the Team</a><a href="#">News</a><a href="#">Careers</a></div>
  <div class="footer-col" style="left:228px"><h4>LET US HELP</h4><a href="#">Training</a><a href="#">Tech Support</a><a href="#">Data Conversions</a><a href="#">Contact Us</a><a href="#">Help Suite</a></div>
  <div class="footer-col" style="left:355px"><h4>THE GOODS</h4><a href="#">Web-Based Software</a><a href="#">Merchant Processing</a><a href="#">Hardware</a><a href="#">ID &amp; Gift Cards</a><a href="#">Mobile Apps</a><a href="#">Finder</a><a href="#">Partnerships</a></div>
  <div class="footer-col" style="left:506px"><h4>CLIENTS</h4><a href="#">Client Finder</a><a href="#">Success Stories</a><a href="#">Refer a Business</a></div>
  <div class="footer-col" style="left:642px"><h4>EDUCATION</h4><a href="#">Halvern University</a><a href="#">Business Consulting</a><a href="#">Webinars</a><a href="#">White Papers</a></div>
  <div class="footer-col" style="left:792px"><h4>COOL STUFF</h4><a href="#">Demo Sites</a><a href="#">Blog</a><a href="#">Videos</a><a href="#">Results Calculator</a></div>
  <div class="footer-brand">Tarvento</div>
  <div class="legal">Copyright ©2001-2011 TARVENTO<br><a href="#">Privacy Notice</a> | <a href="#">Terms of Use</a> | <a href="#">Disclaimer</a></div>
</footer>
</body>
</html>
```